Stationery Design Project for Nimbora, Chicago

Nimbora, a street parking application which helps car drivers find a street parking spot by offering an ideal path along which to look for parking. This path is calculated by our algorithm based on data (e.g. historical data, baseball games schedule, etc.). Along this path the driver will find a spot and will also save 70% of the search time. Customer we target is reg. between 21 and 45 yo.

We envision something young, fresh, bright and original. Slightly abstract maybe. It should represent the idea and elements of finding street parking in the city, e.g. car(s), parking spot, people, city, etc. (just ideas!).

Logo is attached.

Requirement:
- Business Cards (2 Sided Full Color CMYK)
- Letterhead (1 Sided Full Color CMYK)
- Envelope (1 Sided Full Color CMYK)
- Sticker (1 Sided Full Color CMYK), round with a 2inch diameter.

Reason: We're starting to get more and more designs and need more time to look into all of them. Very exciting!! Thanks to everybody!

Hi all, we're in the process of selecting our favs. Though choices!!! Really good submissions. Will keep you posted and sorry for the delay.

Target Market(s)

Car drivers and owners between 21 and 45

Industry/Entity Type

Parking

Requirements
Must have
• Sticker should be round and include company URL nimbora.com and the new logo which we will attach soon.
Should not have
• Should not be too serious or boring.

```html
<!DOCTYPE html>
<html lang="en">
<head>
<meta charset="utf-8">
<title>Nimbora Business Card</title>
<link rel="stylesheet" href="https://fonts.googleapis.com/css2?family=Open+Sans:wght@400;600;700&display=swap">
<style>
  :root {
    --page-bg: #e9eaec;
    --card-light: #ffffff;
    --card-shade: #d9dadc;
    --brand-blue: #2b3fa8;
    --brand-blue-light: #2f7fd6;
    --band-dark: #2a2a2a;
    --band-grey: #6d6d6d;
    --ink: #2b2b2b;
    --ink-soft: #555555;
    --photo-top: #9a9b96;
    --photo-bottom: #6f706c;
  }
  * { margin: 0; padding: 0; box-sizing: border-box; }
  html, body { width: 954px; height: 1200px; overflow: hidden; }
  body {
    background: var(--page-bg);
    font-family: "Open Sans", Arial, sans-serif;
    color: var(--ink);
    position: relative;
  }
  .card {
    position: absolute;
    left: 77px;
    width: 800px;
    height: 456px;
    border-radius: 24px;
    overflow: hidden;
    background: linear-gradient(120deg, var(--card-light) 30%, var(--card-shade) 100%);
    box-shadow: 0 6px 18px rgba(0,0,0,0.25);
  }
  .card--front { top: 99px; }
  .card--back { top: 645px; }
  .card__art { position: absolute; inset: 0; width: 800px; height: 456px; }
  .brand { position: absolute; display: flex; align-items: center; }
  .brand__dot {
    border-radius: 50%;
    background: var(--brand-blue);
  }
  .card--front .brand { left: 190px; top: 70px; gap: 24px; }
  .card--front .brand__dot { width: 150px; height: 150px; }
  .brand__name {
    font-weight: 600;
    font-size: 70px;
    color: var(--ink);
    letter-spacing: -1px;
  }
  .person {
    position: absolute;
    right: 312px;
    top: 290px;
    text-align: right;
  }
  .person__name { font-weight: 700; font-size: 23px; color: var(--ink-soft); line-height: 1.2; }
  .person__role { font-size: 18px; color: var(--ink-soft); line-height: 1.4; }
  .divider {
    position: absolute;
    left: 519px; top: 266px;
    width: 1px; height: 104px;
    background: var(--ink-soft);
  }
  .contacts {
    position: absolute;
    left: 539px; top: 266px;
    list-style: none;
    font-size: 18.5px;
    line-height: 26.5px;
    color: var(--ink-soft);
  }
  .contacts b { font-weight: 700; color: var(--ink); }
  .address {
    position: absolute;
    font-size: 18.5px;
    color: var(--ink-soft);
    white-space: nowrap;
  }
  .card--front .address { right: 43px; top: 395px; }
  .card--back .address { right: 88px; top: 380px; }
  .card--back .brand { left: 175px; top: 150px; flex-direction: column; gap: 12px; }
  .card--back .brand__dot { width: 150px; height: 150px; }
  .card--back .brand__name { font-size: 30px; letter-spacing: 0; }
  .parking-photo {
    position: absolute;
    left: 391px; top: 105px;
    width: 359px; height: 226px;
    background: linear-gradient(160deg, var(--photo-top), var(--photo-bottom));
  }
</style>
</head>
<body>

<section class="card card--front">
  <svg class="card__art" viewBox="0 0 800 456" aria-hidden="true">
    <defs>
      <radialGradient id="blueBand" cx="0.3" cy="0.5" r="0.8">
        <stop offset="0" stop-color="#3f8ce0"/>
        <stop offset="0.6" stop-color="#2b3fa8"/>
        <stop offset="1" stop-color="#1e2a86"/>
      </radialGradient>
    </defs>
    <path d="M0 0 H292 C120 40 40 210 168 456 H0 Z" fill="url(#blueBand)"/>
    <path d="M262 0 C110 60 50 250 150 456" fill="none" stroke="#ffffff" stroke-width="20"/>
    <path d="M232 0 C92 70 52 250 118 456" fill="none" stroke="#2f7fd6" stroke-width="8"/>
  </svg>
  <div class="brand">
    <span class="brand__dot"></span>
    <span class="brand__name">nimbora</span>
  </div>
  <div class="person">
    <p class="person__name">Your Name</p>
    <p class="person__role">Designation</p>
  </div>
  <span class="divider"></span>
  <ul class="contacts">
    <li><b>p</b> : 123-456-7890</li>
    <li><b>c</b> : 123-456-7890</li>
    <li><b>e</b> : name@website.com</li>
    <li><b>w</b> : www.website.com</li>
  </ul>
  <p class="address">City Name, Street Name, State Name, Country Code</p>
</section>

<section class="card card--back">
  <svg class="card__art" viewBox="0 0 800 456" aria-hidden="true">
    <defs>
      <radialGradient id="greyBand" cx="0.3" cy="0.5" r="0.8">
        <stop offset="0" stop-color="#8a8a8a"/>
        <stop offset="0.6" stop-color="#4a4a4a"/>
        <stop offset="1" stop-color="#2a2a2a"/>
      </radialGradient>
    </defs>
    <path d="M0 0 H292 C120 40 40 210 168 456 H0 Z" fill="url(#greyBand)"/>
    <path d="M262 0 C110 60 50 250 150 456" fill="none" stroke="#ffffff" stroke-width="20"/>
    <path d="M232 0 C92 70 52 250 118 456" fill="none" stroke="#111111" stroke-width="10"/>
  </svg>
  <div class="brand">
    <span class="brand__dot"></span>
    <span class="brand__name">nimbora</span>
  </div>
  <div class="parking-photo" role="img" aria-label="Photo of cars parked in street parking bays seen from above"></div>
  <p class="address">City Name, Street Name, State Name, Country Code</p>
</section>

</body>
</html>
```